Fern Lattice Table & Chair Rentals

We need a business card for a table and chair rental company. We rent tables and chairs for weddings, funerals, business events and parties. We want something that looks clean and elegant while not being too busy. We would like colors in the green and blue hues and avoiding anything orange. We want to make sure the font is large enough to be seen easily.

Target Market(s)

Wedding & Event Rentals

Industry/Entity Type

Events

Contact Information for Business Card

Fern Lattice, sales@fernlatticerentals.com, fernlatticerentals.com, 360-555-0182

Requirements
Must have
• Easy to read font
Should not have
• Orange anywhere in the design

```html
<!DOCTYPE html>
<html lang="en">
<head>
<meta charset="utf-8">
<title>Fern Lattice Table &amp; Chair Rentals – Business Card</title>
<link rel="stylesheet" href="https://fonts.googleapis.com/css2?family=Open+Sans:wght@400;600&display=swap">
<style>
  :root {
    --backdrop: #2b2b2c;
    --card: #ffffff;
    --ink: #2f2a1e;
    --bark: #3a3020;
    --leaf: #6b9a1e;
    --shadow: rgba(0, 0, 0, 0.45);
  }
  * { box-sizing: border-box; margin: 0; padding: 0; }
  html, body {
    width: 1200px;
    height: 852px;
    overflow: hidden;
    background: var(--backdrop);
    font-family: "Open Sans", Arial, sans-serif;
    color: var(--ink);
  }
  .stage {
    width: 1200px;
    height: 852px;
    display: flex;
    align-items: center;
    justify-content: center;
    gap: 60px;
  }
  .card {
    position: relative;
    width: 520px;
    height: 297px;
    background: var(--card);
    border-radius: 22px;
    overflow: hidden;
    box-shadow: 0 12px 30px var(--shadow);
  }

  /* Front */
  .card--front {
    display: flex;
    flex-direction: column;
    align-items: center;
    justify-content: center;
  }
  .brand-name {
    font-weight: 400;
    color: var(--ink);
    letter-spacing: 0.5px;
  }
  .card--front .brand-name { font-size: 52px; line-height: 1.1; }
  .tagline {
    margin-top: 10px;
    font-size: 22px;
    font-weight: 400;
    color: var(--ink);
  }

  /* Back */
  .side-band {
    position: absolute;
    top: 0; left: 0; bottom: 0;
    width: 38px;
    background: var(--bark);
  }
  .side-rule {
    position: absolute;
    top: 0; bottom: 0;
    left: 38px;
    width: 6px;
    background: var(--leaf);
  }
  .card--back .brand-name {
    position: absolute;
    top: 34px;
    left: 72px;
    font-size: 34px;
  }
  .contact-list {
    position: absolute;
    left: 150px;
    bottom: 36px;
    list-style: none;
    display: flex;
    flex-direction: column;
    gap: 6px;
  }
  .contact-item {
    display: flex;
    align-items: center;
    gap: 10px;
    font-size: 17px;
    color: var(--ink);
  }
  .contact-icon { width: 16px; height: 16px; flex: none; }
  .contact-icon * { fill: var(--leaf); }
</style>
</head>
<body>
<main class="stage">
  <section class="card card--front" aria-label="Card front">
    <h1 class="brand-name">Fern Lattice</h1>
    <p class="tagline">Table and Chair Rentals</p>
  </section>

  <section class="card card--back" aria-label="Card back">
    <div class="side-band"></div>
    <div class="side-rule"></div>
    <h2 class="brand-name">Fern Lattice</h2>
    <ul class="contact-list">
      <li class="contact-item">
        <svg class="contact-icon" viewBox="0 0 16 16" aria-hidden="true">
          <path d="M1 5c0-2 2-3 7-3s7 1 7 3v1h-4V4.5C9.8 4.2 6.2 4.2 5 4.5V6H1z"/>
          <path d="M4 7h8l2 7H2z"/>
        </svg>
        360-555-0182
      </li>
      <li class="contact-item">
        <svg class="contact-icon" viewBox="0 0 16 16" aria-hidden="true">
          <path d="M1 3h14v1.2L8 9 1 4.2z"/>
          <path d="M1 5.6 8 10.4l7-4.8V13H1z"/>
        </svg>
        sales@fernlatticerentals.com
      </li>
      <li class="contact-item">
        <svg class="contact-icon" viewBox="0 0 16 16" aria-hidden="true">
          <path d="M8 1a7 7 0 1 0 0 14A7 7 0 0 0 8 1zm0 1.5c.8 0 1.7 1.5 2 4H6c.3-2.5 1.2-4 2-4zM2.6 6.5h2c-.1.5-.1 1-.1 1.5s0 1 .1 1.5h-2a5.6 5.6 0 0 1 0-3zm3.4 3h4c-.3 2.5-1.2 4-2 4s-1.7-1.5-2-4zm5.4 0c.1-.5.1-1 .1-1.5s0-1-.1-1.5h2a5.6 5.6 0 0 1 0 3z"/>
        </svg>
        www.fernlatticerentals.com
      </li>
    </ul>
  </section>
</main>
</body>
</html>
```